New Business Card Design Project

We require a business card design for Vexalund, a newly established Indian company.
Our focus is on the development, manufacturing, and export of a diverse array of pharmaceutical products on a global scale. The card should convey a professional appearance, as our primary markets are in Africa, China, and Southeast Asian nations.
We envision a two-sided business card, with the reverse side dedicated to a logo set against a solid color or an elegantly designed pattern. The corners should be rounded. We would appreciate seeing both horizontal and vertical design options. We trust the designer to utilize their expertise in creating this design.

The content for the business card is included in the attached Word file.

Target Market(s)

Our primary markets are in Africa, China, and Southeast Asian, Latin America, Maldives, Sri Lanka

Industry/Entity Type

Pharmaceutical Manufacturing and Export

Contact Information for Business Card

Colors

Designer to choose colors to be used in the design.

Requirements
Must have
• The reverse side of the business card features solely the logo along with the tagline, "Cures for Living."
Should not have
• The logo should not exceed two instances, encompassing both the front and back sides of the card.

```html
<!DOCTYPE html>
<html lang="en">
<head>
<meta charset="utf-8">
<title>Vexalund Business Card</title>
<link href="https://fonts.googleapis.com/css2?family=Karla:wght@400;500;700&display=swap" rel="stylesheet">
<style>
  :root {
    --bg: #2a2a2a;
    --brand-blue: #2a9fd6;
    --brand-blue-deep: #2590c4;
    --brand-red: #e05a45;
    --paper: #f1f1f1;
    --ink: #333333;
    --white: #f4f4f4;
  }
  * { margin: 0; padding: 0; box-sizing: border-box; }
  html, body {
    width: 1200px; height: 1138px; overflow: hidden;
    background: var(--bg);
    font-family: "Karla", Arial, sans-serif;
  }
  .canvas { position: relative; width: 1200px; height: 1138px; }
  .card {
    position: absolute;
    width: 622px; height: 376px;
    border-radius: 18px;
    overflow: hidden;
  }
  /* Back side */
  .card--back { left: 274px; top: 185px; background: var(--brand-blue); }
  .back-mark {
    position: absolute; left: 278px; top: 110px;
    width: 66px; height: 66px; border-radius: 50%;
    background: var(--white);
  }
  .back-name {
    position: absolute; left: 0; right: 0; top: 226px;
    text-align: center; color: var(--white);
    font-weight: 700; font-size: 66px; line-height: 1; letter-spacing: -0.5px;
  }
  .back-tagline {
    position: absolute; left: 0; right: 0; top: 284px;
    text-align: center; color: var(--white);
    font-size: 15px; line-height: 1; letter-spacing: 12px; padding-left: 12px;
  }
  /* Front side */
  .card--front { left: 276px; top: 608px; background: var(--paper); }
  .front-mark {
    position: absolute; left: 138px; top: 122px;
    width: 74px; height: 74px; border-radius: 50%;
    background: var(--brand-blue);
  }
  .front-name {
    position: absolute; left: 54px; top: 222px;
    color: var(--brand-blue-deep);
    font-weight: 700; font-size: 57px; line-height: 1; letter-spacing: -0.5px;
  }
  .person-name {
    position: absolute; left: 352px; top: 87px;
    color: var(--brand-blue); font-weight: 700; font-size: 24px; line-height: 1;
  }
  .person-role {
    position: absolute; left: 352px; top: 120px;
    color: var(--ink); font-size: 16px; font-weight: 400; line-height: 1;
  }
  .contact-list { position: absolute; left: 352px; top: 167px; list-style: none; }
  .contact-item {
    display: flex; align-items: center; height: 22.5px;
    color: var(--ink); font-size: 16px;
  }
  .contact-item svg { width: 16px; height: 14px; margin: 0 14px 0 2px; flex: none; }
  .address {
    position: absolute; left: 353px; top: 242px;
    color: var(--ink); font-size: 16px; line-height: 22px; font-style: normal;
  }
  .footer-band { position: absolute; left: 0; bottom: 0; width: 622px; height: 48px; }
  .footer-tagline {
    position: absolute; left: 346px; top: 343px;
    color: var(--white); font-size: 16px; line-height: 1;
  }
</style>
</head>
<body>
<main class="canvas">
  <section class="card card--back" aria-label="Card back">
    <div class="back-mark"></div>
    <div class="back-name">Vexalund</div>
    <div class="back-tagline">CURES FOR LIVING</div>
  </section>

  <section class="card card--front" aria-label="Card front">
    <div class="front-mark"></div>
    <div class="front-name">Vexalund</div>

    <h1 class="person-name">Arjun K. Malvade</h1>
    <p class="person-role">CEO, Vexalund</p>

    <ul class="contact-list">
      <li class="contact-item">
        <svg viewBox="0 0 16 14" aria-hidden="true"><path fill="var(--brand-red)" d="M1 4c0-2 3-3 7-3s7 1 7 3v1h-3.5V3.5h-7V5H1zM4 6h8l2 7H2z"/><circle cx="8" cy="9.5" r="1.8" fill="var(--paper)"/></svg>
        +91-9876501234
      </li>
      <li class="contact-item">
        <svg viewBox="0 0 16 14" aria-hidden="true"><rect x="1" y="2" width="14" height="10" fill="var(--brand-red)"/><path d="M1 2l7 6 7-6M1 12l5-5M15 12l-5-5" stroke="var(--paper)" stroke-width="1.2" fill="none"/></svg>
        amalvade@vexalund.com
      </li>
      <li class="contact-item">
        <svg viewBox="0 0 16 14" aria-hidden="true"><circle cx="8" cy="7" r="6" fill="var(--brand-red)"/><path d="M2 7h12M8 1v12M4 3.5h8M4 10.5h8M8 1c-3 3-3 9 0 12M8 1c3 3 3 9 0 12" stroke="var(--paper)" stroke-width="0.8" fill="none"/></svg>
        https://vexalund.com
      </li>
    </ul>

    <address class="address">12, Sunrise Colony,<br>Nagpur-440010 (INDIA)</address>

    <svg class="footer-band" viewBox="0 0 622 48" preserveAspectRatio="none" aria-hidden="true">
      <rect x="0" y="32" width="290" height="16" fill="var(--brand-red)"/>
      <polygon points="290,0 622,0 622,48 264,48" fill="var(--brand-blue-deep)"/>
    </svg>
    <div class="footer-tagline">Cures for Living.</div>
  </section>
</main>
</body>
</html>
```